Computer consultant business card

Bexil Software is a newly started computer consulting company. It's a small one-man company that provides mostly Vornix applications but also websites in collaboration with designers. I'm running this company on the side of full time university studies.

I want the final design to be clean and memorable. Be creative! :)

Some inspiration:
http://www.pixelmarta.com/design/48317
http://www.pixelmarta.com/design/2739164/business-card-design-by-frostlynk
http://www.pixelmarta.com/design/604281/business-card-design-by-koralind-vestrabanu

See attachment for my company logo.
Updates

I would like to thank everyone for submitting! I'll need a couple of days to review and ultimately select a design.

Target Market(s)

Non-technical entrepreneurs and small companies.

Industry/Entity Type

University

Requirements
Must have
• My company logo.
In any way, both colors from my logo.
First- and last name, e-mail and phone number.
Double-sided design.
Nice to have
• Something creative with the symbol in my logo

```html
<!DOCTYPE html>
<html lang="en">
<head>
<meta charset="utf-8">
<title>Bexil Software – Business Card Concepts</title>
<link href="https://fonts.googleapis.com/css2?family=Open+Sans:wght@400;600;700&display=swap" rel="stylesheet">
<style>
  :root {
    --stage: #ecebe8;
    --ink: #333235;
    --ink-soft: #4a4a4d;
    --brand-blue: #4472c4;
    --white: #ffffff;
    --black: #050505;
    --slate-top: #2d2e34;
    --slate-glow: #4b5b86;
    --label: #1d1d1d;
  }
  * { box-sizing: border-box; margin: 0; padding: 0; }
  html, body {
    width: 1200px; height: 788px; overflow: hidden;
    background: var(--stage);
    font-family: "Open Sans", Arial, sans-serif;
  }
  .sheet { position: relative; width: 1200px; height: 788px; }

  .sheet-label {
    position: absolute; width: 525px; text-align: center;
    font-size: 20px; font-weight: 400; color: var(--label);
  }
  .card {
    position: absolute; width: 525px; height: 298px;
    border-radius: 22px; overflow: hidden;
    box-shadow: 0 3px 8px rgba(0,0,0,.25);
  }
  .card--front  { left: 54px;  top: 75px;  background: var(--white); }
  .card--back-1 { left: 622px; top: 75px;  background: var(--white); }
  .card--back-2 { left: 54px;  top: 446px; background: var(--black); }
  .card--back-3 {
    left: 622px; top: 446px;
    background: radial-gradient(ellipse 90% 95% at 50% 100%, var(--slate-glow) 0%, #3c4660 45%, var(--slate-top) 100%);
  }

  /* Wordmark: plain circle + name */
  .brand { position: absolute; display: flex; align-items: center; gap: 22px; }
  .brand__dot { width: 98px; height: 98px; border-radius: 50%; background: var(--brand-blue); }
  .brand__name {
    font-size: 78px; font-weight: 600; line-height: 1; letter-spacing: 1px;
    color: var(--ink);
  }
  .brand--light .brand__name { color: var(--white); }
  .brand--large .brand__dot { width: 106px; height: 106px; }
  .brand--large .brand__name { font-size: 84px; }

  .card--front .brand  { left: 106px; top: 22px; }
  .card--back-1 .brand,
  .card--back-2 .brand,
  .card--back-3 .brand { left: 104px; top: 92px; }

  .website {
    position: absolute; left: 0; right: 0; top: 248px;
    text-align: center; font-size: 18px; letter-spacing: 4px;
    color: var(--ink-soft);
  }
  .website--light { color: var(--white); top: 254px; }

  .contact { position: absolute; left: 184px; top: 166px; color: var(--ink-soft); font-size: 15px; }
  .contact__row { display: flex; align-items: center; gap: 9px; height: 21px; letter-spacing: .5px; }
  .contact__icon { width: 11px; height: 11px; fill: var(--ink-soft); }

  .front-swoosh { position: absolute; left: 0; top: 0; width: 525px; height: 298px; }
  .holder {
    position: absolute; right: 60px; top: 250px; width: 230px;
    text-align: center; color: var(--white);
  }
  .holder__name { font-size: 17px; font-weight: 700; line-height: 1.2; }
  .holder__role { font-size: 12.5px; line-height: 1.4; }

  .dot-texture { position: absolute; inset: 0; }
  .dot-texture--top {
    background: radial-gradient(ellipse 45% 40% at 28% 0%, rgba(95,95,100,.55), rgba(0,0,0,0) 70%);
  }
  .dot-texture--bottom {
    background: radial-gradient(ellipse 40% 45% at 80% 100%, rgba(120,115,120,.55), rgba(0,0,0,0) 70%);
  }
  .card--back-2 .brand, .card--back-2 .website { z-index: 1; }
</style>
</head>
<body>
<main class="sheet">

  <p class="sheet-label" style="left:54px; top:34px;">Front</p>
  <p class="sheet-label" style="left:622px; top:34px;">Back - 1</p>
  <p class="sheet-label" style="left:54px; top:404px;">Back - 2</p>
  <p class="sheet-label" style="left:622px; top:404px;">Back - 3</p>

  <!-- Front -->
  <section class="card card--front">
    <div class="brand">
      <span class="brand__dot"></span>
      <span class="brand__name">bexil</span>
    </div>

    <div class="contact">
      <div class="contact__row">
        <svg class="contact__icon" viewBox="0 0 12 12" aria-hidden="true"><path d="M2.5 0.5 4.5 3 3.4 4.3c.8 1.7 2.2 3.1 4.3 4.3L9 7.5l2.5 2-1.4 2C5.5 11 1 6.5.5 1.9z"/></svg>
        <span>+12 345 6789</span>
      </div>
      <div class="contact__row">
        <svg class="contact__icon" viewBox="0 0 12 12" aria-hidden="true"><path d="M1 3h10v7H1z M1 3l5 4 5-4" stroke="#fff" stroke-width=".8"/></svg>
        <span>info@website.com</span>
      </div>
    </div>

    <svg class="front-swoosh" viewBox="0 0 525 298" aria-hidden="true">
      <path d="M0 266 Q120 247 270 241 Q140 257 0 290 Z" fill="var(--brand-blue)"/>
      <path d="M0 298 L0 294 Q200 252 525 236 L525 298 Z" fill="var(--ink)"/>
    </svg>
    <div class="holder">
      <p class="holder__name">First Name + Last Name</p>
      <p class="holder__role">Designation</p>
    </div>
  </section>

  <!-- Back 1 -->
  <section class="card card--back-1">
    <div class="brand brand--large">
      <span class="brand__dot"></span>
      <span class="brand__name">bexil</span>
    </div>
    <p class="website">www.website.com</p>
  </section>

  <!-- Back 2 -->
  <section class="card card--back-2">
    <div class="dot-texture dot-texture--top" role="img" aria-label="Perforated metal dot texture fading in from the top edge"></div>
    <div class="dot-texture dot-texture--bottom" role="img" aria-label="Perforated metal dot texture fading in from the bottom right corner"></div>
    <div class="brand brand--large brand--light">
      <span class="brand__dot"></span>
      <span class="brand__name">bexil</span>
    </div>
    <p class="website website--light">www.website.com</p>
  </section>

  <!-- Back 3 -->
  <section class="card card--back-3">
    <div class="brand brand--large brand--light">
      <span class="brand__dot"></span>
      <span class="brand__name">bexil</span>
    </div>
    <p class="website website--light">www.website.com</p>
  </section>

</main>
</body>
</html>
```